Blue Heron Journeys

We are a predominantly online travel agency with high-end (first/business class) clients. I'm looking to either have our existing logo revamped or a new logo created with business card layout. I prefer to work with existing logo if possible so it remains familiar with existing clientele. I have uploaded a yellow business card layout showing icons on one side of the card. I would like to keep my existing colours, not yellow. could the company name/tag line go over the icons?
Industry/Entity Type
Business
Contact Information for Business Card
Lucinda Fairley
Director
(I.A.T.A. 07715463)
(Corvano Pty. Ltd) ABN 61 574 203 918
512/18 Kendrick Lane
Wattle Reach | NSW 2577 | Australia
www.blueheronjourneys.com.au
m: + 61 (0) 417 588 130
t: + 61 (0) 2 9416 2058
e: lucinda@blueheronjourneys.com.au

```html
<!DOCTYPE html>
<html lang="en">
<head>
<meta charset="utf-8">
<title>Blue Heron Journeys – Business Card</title>
<link rel="stylesheet" href="https://fonts.googleapis.com/css2?family=Dancing+Script:wght@700&family=Roboto:ital,wght@0,400;0,500;1,400&display=swap">
<style>
  :root {
    --backdrop: #232323;
    --card: #fefefd;
    --card-back: #fdfbf2;
    --logo-field: #fbead0;
    --ink: #111111;
    --text: #4a4a4a;
    --muted: #555555;
  }
  * { margin: 0; padding: 0; box-sizing: border-box; }
  html, body {
    width: 1200px; height: 960px; overflow: hidden;
    background: var(--backdrop);
    font-family: "Roboto", Arial, sans-serif;
  }
  .canvas { position: relative; width: 1200px; height: 960px; }
  .card { position: absolute; width: 600px; height: 343px; }
  .card--front { left: 314px; top: 113px; background: var(--card); }
  .card--back { left: 311px; top: 472px; background: var(--card-back); }

  .logo {
    position: absolute;
    display: flex; align-items: center; justify-content: center;
    background: var(--logo-field);
    color: var(--ink);
    font-family: "Roboto", Arial, sans-serif;
    font-weight: 500;
    white-space: nowrap;
  }
  .card--front .logo { left: 42px; top: 42px; width: 248px; height: 95px; font-size: 21px; }
  .card--back .logo { left: 156px; top: 122px; width: 285px; height: 110px; font-size: 24px; }

  .address {
    position: absolute; left: 42px; top: 164px;
    font-size: 14.5px; line-height: 18px; color: var(--text);
  }
  .contacts {
    position: absolute; left: 42px; top: 207px;
    list-style: none; font-size: 14.5px; line-height: 18.5px; color: var(--text);
    white-space: nowrap;
  }
  .contacts li { display: flex; align-items: center; gap: 9px; }
  .contacts svg { width: 14px; height: 14px; fill: var(--ink); flex: none; }

  .person {
    position: absolute; right: 45px; top: 206px; text-align: right;
  }
  .person__name {
    font-family: "Dancing Script", cursive; font-weight: 700;
    font-size: 40px; line-height: 44px; color: var(--ink);
  }
  .person__role { font-size: 15px; font-weight: 500; color: var(--muted); letter-spacing: 0.2px; }

  .edge-bars { position: absolute; right: 0; top: 214px; width: 15px; }
  .edge-bars span { display: block; height: 5px; margin-bottom: 4px; background: var(--ink); }

  .web {
    position: absolute; left: 0; right: 0; top: 263px; text-align: center;
    font-style: italic; font-size: 15px; letter-spacing: 3px; color: var(--text);
  }
</style>
</head>
<body>
<main class="canvas">
  <section class="card card--front" aria-label="Business card front">
    <div class="logo">Blue Heron Journeys</div>
    <p class="address">512/18 Kendrick Lane<br>Wattle Reach | NSW 2577 | Australia</p>
    <ul class="contacts">
      <li><svg viewBox="0 0 24 24"><path d="M6.6 10.8a15.1 15.1 0 0 0 6.6 6.6l2.2-2.2c.3-.3.7-.4 1-.2 1.1.4 2.3.6 3.6.6.6 0 1 .4 1 1V20c0 .6-.4 1-1 1A17 17 0 0 1 3 4c0-.6.4-1 1-1h3.5c.6 0 1 .4 1 1 0 1.3.2 2.5.6 3.6.1.3 0 .7-.2 1z"/></svg>+ 61 (0) 2 9416 2058</li>
      <li><svg viewBox="0 0 24 24"><path d="M7 1h10a2 2 0 0 1 2 2v18a2 2 0 0 1-2 2H7a2 2 0 0 1-2-2V3a2 2 0 0 1 2-2zm0 3v14h10V4zm5 15.5a1 1 0 1 0 0 2 1 1 0 0 0 0-2z"/></svg>+ 61 (0) 417 588 130</li>
      <li><svg viewBox="0 0 24 24"><path d="M4 4h16v16H4zm3 4v2h10V8zm0 4v2h10v-2zm0 4v1h6v-1z"/></svg>I.A.T.A. 07715463</li>
      <li><svg viewBox="0 0 24 24"><path d="M4 4h16v16H4zm3 4v2h10V8zm0 4v2h10v-2zm0 4v1h6v-1z"/></svg>Corvano Pty. Ltd &nbsp;ABN 61 574 203 918</li>
      <li><svg viewBox="0 0 24 24"><path d="M2 5h20v14H2zm2 2v.5l8 5 8-5V7zm0 2.9V17h16V9.9l-8 5z"/></svg>lucinda@blueheronjourneys.com.au</li>
      <li><svg viewBox="0 0 24 24"><path d="M12 2a10 10 0 1 0 0 20 10 10 0 0 0 0-20zm-1 17.9A8 8 0 0 1 4.2 10L9 14.8v1a2 2 0 0 0 2 2zm6.9-2.5a2 2 0 0 0-1.9-1.4h-1v-3a1 1 0 0 0-1-1H8v-2h2a1 1 0 0 0 1-1V7h2a2 2 0 0 0 2-2v-.4a8 8 0 0 1 2.9 12.8z"/></svg>www.blueheronjourneys.com.au</li>
    </ul>
    <div class="person">
      <p class="person__name">Lucinda Fairley</p>
      <p class="person__role">DIRECTOR</p>
    </div>
    <div class="edge-bars" aria-hidden="true"><span></span><span></span><span></span><span></span><span></span><span></span></div>
  </section>

  <section class="card card--back" aria-label="Business card back">
    <div class="logo">Blue Heron Journeys</div>
    <p class="web">www.blueheronjourneys.com.au</p>
  </section>
</main>
</body>
</html>
```